Newsletter template

I am looking for 2 newsletter templates. My website is in Wordpress and I want to use in mailchimp for lists.

One newsletter is for local clients of design remodeling firm to be sent monthly

Second newsletter is for web store offerings to be sent weekly.

Target Market(s)

Luxury home and leisure

Industry/Entity Type

Store

Requirements
Must have
• Use logos and colors to seamlessly integrate with website,

```html
<!DOCTYPE html>
<html lang="en">
<head>
<meta charset="utf-8">
<title>Mira Lane — New Products Newsletter</title>
<link rel="stylesheet" href="https://fonts.googleapis.com/css2?family=Arimo:wght@400;700&display=swap">
<style>
  :root {
    --ink: #444444;
    --body: #777777;
    --accent: #1aaccc;
    --lime: #d9dc00;
    --bar: #454545;
    --paper: #ffffff;
    --rule: #e2e2e2;
    --link: #3a9ac9;
  }
  * { box-sizing: border-box; margin: 0; padding: 0; }
  html, body { width: 698px; height: 1200px; overflow: hidden; background: var(--paper); }
  body { font-family: "Arimo", Arial, sans-serif; color: var(--body); position: relative; }

  .topbar-tab {
    position: absolute; left: 53px; top: 0; width: 184px; height: 64px;
    background: linear-gradient(#555, #2e2e2e);
    color: #fff; font-size: 17px; text-align: center; line-height: 70px;
    box-shadow: 0 4px 6px rgba(0,0,0,.15);
  }
  .topbar-tab::after {
    content: ""; position: absolute; left: 0; right: 0; bottom: 4px;
    border-top: 1px dashed #888;
  }
  .topbar-tab::before {
    content: ""; position: absolute; left: 0; right: 0; top: 4px;
    border-top: 1px dashed #666;
  }
  .utility-links {
    position: absolute; right: 54px; top: 8px; font-size: 10.5px; color: var(--body);
  }
  .utility-links a { color: var(--link); text-decoration: none; }

  .brand {
    position: absolute; left: 0; right: 0; top: 66px; text-align: center;
    font-size: 34px; font-weight: 400; color: var(--accent); letter-spacing: 1px;
  }

  .divider {
    position: absolute; left: 53px; width: 591px; height: 12px;
    background: radial-gradient(ellipse at center, #dcdcdc 0%, rgba(255,255,255,0) 70%);
  }
  .divider::after {
    content: ""; position: absolute; left: 0; right: 0; top: 5px;
    border-top: 2px dotted #d4d4d4;
  }

  .intro { position: absolute; left: 53px; top: 184px; width: 591px; }
  .intro h1 { font-size: 16.5px; font-weight: 400; color: var(--accent); margin-bottom: 3px; }
  .intro p { width: 360px; font-size: 14px; line-height: 20.7px; color: var(--body); }
  .intro-image {
    position: absolute; left: 396px; top: 12px; width: 184px; height: 121px; background: #454545;
  }

  .product { position: absolute; left: 53px; width: 591px; height: 342px; }
  .product-bar {
    position: absolute; left: 0; top: 0; width: 591px; height: 42px; background: var(--bar);
    color: #fff; font-size: 15px; font-weight: 700; line-height: 42px; padding-left: 12px;
  }
  .product-price {
    position: absolute; right: 0; top: 0; width: 97px; height: 42px; background: var(--accent);
    color: #fff; font-size: 15px; font-weight: 700; line-height: 42px; text-align: center;
  }
  .product-badge {
    position: absolute; left: 0; top: 61px; height: 21px; padding: 0 8px;
    background: var(--lime); color: #fff; font-size: 10px; font-weight: 700; line-height: 21px;
  }
  .product-image {
    position: absolute; left: 50px; top: 100px; width: 190px; height: 165px;
    background: radial-gradient(ellipse at 50% 60%, #e4e4e4 0%, #f3f3f3 45%, #fff 75%);
  }
  .product-copy { position: absolute; left: 305px; top: 58px; width: 286px; }
  .product-copy p { font-size: 11.5px; line-height: 18.7px; color: var(--body); }
  .feature-list { list-style: none; margin-top: 10px; }
  .feature-list li {
    display: flex; align-items: center; gap: 7px; height: 38.5px;
    border-bottom: 1px dotted var(--rule); color: var(--accent); font-size: 11.5px;
  }
  .feature-icon {
    width: 18px; height: 18px; border-radius: 50%; background: #444;
    color: #bbb; font-size: 5.5px; line-height: 18px; text-align: center; flex: none;
  }
  .actions { position: absolute; top: 297px; left: 346px; display: flex; gap: 6px; }
  .btn {
    height: 21px; font-size: 10px; font-weight: 700; color: #fff; text-align: center;
    line-height: 21px; border-bottom: 2px solid rgba(0,0,0,.25);
  }
  .btn-view { width: 60px; background: linear-gradient(#8a8a8a, #6c6c6c); }
  .btn-order { width: 67px; background: linear-gradient(#4a4a4a, #2f2f2f); }
  .btn-buy { width: 60px; background: linear-gradient(#35c2e0, #1aa8c8); }
</style>
</head>
<body>
  <div class="topbar-tab">new products</div>
  <div class="utility-links"><a href="#">browser version</a> • <a href="#">text version</a> • <a href="#">unsubscribe</a></div>
  <div class="brand">Mira Lane</div>

  <div class="divider" style="top:155px"></div>

  <section class="intro">
    <h1>Vivamus pretium diam</h1>
    <p>Suspendisse potenti. Suspendisse sed turpis id arcu fermentum suscipit. Pellentesque scelerisque auctor quam in faucibus. Donec mattis adipiscing lectus ac sodales. Suspendisse potenti. Ut sed nulla in lorem gravida porta ut feugiat magna. Donec et nisi metus, vel varius massa.</p>
    <div class="intro-image" role="img" aria-label="Featured interior photograph"></div>
  </section>

  <div class="divider" style="top:348px"></div>

  <article class="product" style="top:385px">
    <div class="product-bar">First product name 1</div>
    <div class="product-price">608$</div>
    <div class="product-badge">BRAND NEW EDITION</div>
    <div class="product-image" role="img" aria-label="Product photograph: white book standing on a stack of books"></div>
    <div class="product-copy">
      <p>Donec porttitor quam vel purus venenatis rutrum. Nullam quam nibh, congue sed aliquet posuere, aliquam non lacus. Maecenas nec luctus neque. Aliquam sagittis tincidunt lectus, non semper lorem sollicitudin ac. Proin ac felis tortor, eu ultricies orci.</p>
      <ul class="feature-list">
        <li><span class="feature-icon">ICO</span>Proin ac felis tortor, eu ultricies orci</li>
        <li><span class="feature-icon">ICO</span>Aliquam sagittis tincidunt lectus</li>
        <li><span class="feature-icon">ICO</span>Donec porttitor quam vel purus venenatis rutrum</li>
      </ul>
    </div>
    <div class="actions">
      <div class="btn btn-view">VIEW</div>
      <div class="btn btn-order">ORDER</div>
      <div class="btn btn-buy">BUY</div>
    </div>
  </article>

  <div class="divider" style="top:721px"></div>

  <article class="product" style="top:762px">
    <div class="product-bar">Another product 2</div>
    <div class="product-price">280$</div>
    <div class="product-badge">NEW VERSION</div>
    <div class="product-image" role="img" aria-label="Product photograph: white book standing on a stack of books"></div>
    <div class="product-copy">
      <p>Donec porttitor quam vel purus venenatis rutrum. Nullam quam nibh, congue sed aliquet posuere, aliquam non lacus. Maecenas nec luctus neque. Aliquam sagittis tincidunt lectus, non semper lorem sollicitudin ac. Proin ac felis tortor, eu ultricies orci.</p>
      <ul class="feature-list">
        <li><span class="feature-icon">ICO</span>Proin ac felis tortor, eu ultricies orci</li>
        <li><span class="feature-icon">ICO</span>Aliquam sagittis tincidunt lectus</li>
        <li><span class="feature-icon">ICO</span>Donec porttitor quam vel purus venenatis rutrum</li>
      </ul>
    </div>
    <div class="actions">
      <div class="btn btn-view">VIEW</div>
      <div class="btn btn-order">ORDER</div>
      <div class="btn btn-buy">BUY</div>
    </div>
  </article>

  <div class="divider" style="top:1098px"></div>

  <article class="product" style="top:1139px; height:61px">
    <div class="product-bar">Product name 3</div>
    <div class="product-price">495$</div>
  </article>
</body>
</html>
```